mobile app - telecom industry

We are a tech/service company. Our product is a mobile application for physical site inspection called “Vorn”. Our target industry is telecommunica...

Target Market(s)

telecommunication

Industry/Entity Type

Industry

Requirements
Must have
• Screen size Quorin 5 - Android
• Suggest 3 colors
• Design 9 pages

```html
<!DOCTYPE html>
<html lang="en">
<head>
<meta charset="utf-8">
<title>Vorn – Home</title>
<link rel="stylesheet" href="https://fonts.googleapis.com/css2?family=Open+Sans:wght@300;400;600&display=swap">
<style>
  :root {
    --teal: #47b3a8;
    --teal-line: #bfe3df;
    --white: #ffffff;
    --page: #ececec;
    --skyline: #e1e1e1;
  }
  * { box-sizing: border-box; margin: 0; padding: 0; }
  html, body {
    width: 1200px; height: 1200px; overflow: hidden;
    background: var(--page);
    font-family: "Open Sans", sans-serif;
  }
  .app-screen {
    position: absolute; left: 283px; top: 40px;
    width: 634px; height: 1121px;
    background: var(--white);
    overflow: hidden;
  }
  .status-bar {
    height: 30px; background: var(--teal); color: var(--white);
    font-size: 17px; font-weight: 300;
    display: flex; align-items: center; justify-content: space-between;
    padding: 0 10px 0 8px;
  }
  .status-bar .carrier { display: flex; align-items: center; gap: 8px; }
  .status-bar .battery { display: flex; align-items: center; gap: 10px; }
  .battery-bar { width: 40px; height: 10px; background: var(--white); border-radius: 1px; }
  .nav-bar {
    height: 79px; background: var(--teal); color: var(--white);
    display: flex; align-items: center; gap: 22px; padding-left: 30px;
  }
  .nav-title { font-size: 38px; font-weight: 300; letter-spacing: 1px; }
  .tile {
    position: absolute; width: 278px; height: 194px;
    border: 2px solid var(--teal-line);
    display: flex; flex-direction: column; align-items: center; justify-content: center;
    color: var(--teal); background: var(--white); z-index: 2;
  }
  .tile-label { font-size: 37px; font-weight: 400; line-height: 1.1; }
  .tile-count { font-size: 50px; font-weight: 600; line-height: 1.05; }
  .tile svg { fill: none; stroke: var(--teal); stroke-width: 2; }
  .tile-open-a { left: 19px; top: 130px; }
  .tile-create { left: 336px; top: 130px; }
  .tile-open-b { left: 19px; top: 355px; }
  .tile-sync { left: 335px; top: 355px; }
  .tile-settings { left: 19px; top: 580px; }
  .skyline-art {
    position: absolute; left: 0; bottom: 0; width: 100%; height: 420px;
    background: linear-gradient(180deg, rgba(225,225,225,0) 0%, var(--skyline) 45%, var(--skyline) 100%);
    z-index: 1;
  }
</style>
</head>
<body>
  <main class="app-screen">
    <div class="status-bar">
      <span class="carrier">●●●●● Telvo
        <svg width="26" height="16" viewBox="0 0 26 16"><path d="M2 6a16 16 0 0 1 22 0M6 10a10 10 0 0 1 14 0" stroke="#fff" stroke-width="2.5" fill="none"/><circle cx="13" cy="13.5" r="2.5" fill="#fff"/></svg>
      </span>
      <span class="clock">11:59</span>
      <span class="battery">100% <span class="battery-bar"></span></span>
    </div>
    <header class="nav-bar">
      <svg width="26" height="48" viewBox="0 0 26 48"><path d="M24 2 3 24l21 22" stroke="#fff" stroke-width="2" fill="none"/></svg>
      <span class="nav-title">Vorn</span>
    </header>

    <a class="tile tile-open-a">
      <svg width="76" height="62" viewBox="0 0 76 62"><path d="M6 8h20l5 6h36v42H6z"/><path d="M4 20h66l-6 36H2z"/></svg>
      <span class="tile-label">Open WO</span>
      <span class="tile-count">2</span>
    </a>
    <a class="tile tile-create">
      <svg width="68" height="68" viewBox="0 0 68 68"><path d="M34 2v64M2 34h64"/></svg>
      <span class="tile-label" style="margin-top:10px">Create WO</span>
    </a>
    <a class="tile tile-open-b">
      <svg width="70" height="64" viewBox="0 0 70 64"><path d="M3 8h22l5 6h37v47H3z"/></svg>
      <span class="tile-label">Open WO</span>
      <span class="tile-count">2</span>
    </a>
    <a class="tile tile-sync">
      <svg width="64" height="64" viewBox="0 0 64 64" style="stroke-width:3"><path d="M14 18a24 24 0 1 1-3 22"/><path d="M6 12l8 7 8-9"/></svg>
      <span class="tile-label" style="margin-top:10px">Synchronize</span>
    </a>
    <a class="tile tile-settings">
      <svg width="68" height="68" viewBox="0 0 68 68"><circle cx="34" cy="34" r="24" stroke-width="8" stroke-dasharray="7 5.6"/><circle cx="34" cy="34" r="18"/><circle cx="34" cy="34" r="9"/></svg>
      <span class="tile-label" style="margin-top:8px">Settings</span>
    </a>

    <div class="skyline-art" role="img" aria-label="Faint grey city skyline with a telecom transmission tower and dish antennas"></div>
  </main>
</body>
</html>
```